Designing a Chocolate Bar's Package

We are a chocolate manufacturing company located in Lebanon. We produce chocolate on a wholesale level, and we are planning a new line of production at the moment.
We intend to be make small chocolate bars (about 30g) similar to the "Varnou Classica" bar with several flavors. 2 flavors have been decided so far (Mint flavored dark chocolate and Plain dark chocolate).
The packaging material will be similar to varnou's package as well. It won't be a carton box. It'll be some sort of paper wrapping the entire bar. So I am looking for a design that has a unique and cool front and back look.
If only one design is to be prepared, please choose either the mint's flavor or the plain dark chocolate, and prepare the design accordingly.
Updates
Project Deadline Extended
Reason: I still have some time to begin the production. The new deadline,therefore, is the end of this month.
Target Market(s)
basically all chocolate lovers...
Industry/Entity Type
It Company
Requirements
Must have
- I will be uploading our logo. Please make sure to use it in the design.

```html
<!DOCTYPE html>
<html lang="en">
<head>
<meta charset="utf-8">
<title>Corvella Mint Dark Chocolate Wrapper</title>
<link rel="stylesheet" href="https://fonts.googleapis.com/css2?family=Cinzel:wght@500&family=EB+Garamond:wght@500;600;700&display=swap">
<style>
  :root {
    --page: #ffffff;
    --wrap-black: #070806;
    --wrap-green: #1f3a12;
    --wrap-edge-brown: #3a2417;
    --brand-gold: #b48a5c;
    --mint-text: #9fb09a;
    --cocoa-text: #8e5b38;
    --choc-main: #5a2f1b;
    --choc-light: #7a4228;
    --leaf-green: #4f8a2a;
  }
  * { margin: 0; padding: 0; box-sizing: border-box; }
  html, body {
    width: 1200px;
    height: 2275px;
    overflow: hidden;
    background: var(--page);
  }
  .canvas {
    position: relative;
    width: 1200px;
    height: 2275px;
    background: var(--page);
  }
  .wrapper {
    position: absolute;
    left: 99px;
    top: 190px;
    width: 1006px;
    height: 1905px;
    overflow: hidden;
    background:
      radial-gradient(ellipse 55% 40% at 55% 58%, rgba(60,110,30,0.55), rgba(31,58,18,0.25) 55%, transparent 80%),
      linear-gradient(180deg, var(--wrap-black) 0%, #0b1209 55%, var(--wrap-black) 92%, var(--wrap-edge-brown) 100%);
  }
  .brand {
    position: absolute;
    top: 300px;
    left: 0;
    width: 100%;
    text-align: center;
  }
  .brand-name {
    display: inline-flex;
    align-items: center;
    gap: 26px;
    font-family: "EB Garamond", serif;
    font-weight: 600;
    font-size: 170px;
    line-height: 1;
    color: var(--brand-gold);
  }
  .brand-dot {
    width: 54px;
    height: 54px;
    border-radius: 50%;
    background: var(--brand-gold);
  }
  .brand-tagline {
    margin-top: 10px;
    font-family: "EB Garamond", serif;
    font-weight: 500;
    font-size: 40px;
    letter-spacing: 2px;
    color: var(--brand-gold);
  }
  .flavour {
    position: absolute;
    top: 560px;
    left: 0;
    width: 100%;
    text-align: center;
    font-family: "Cinzel", serif;
    font-weight: 500;
    font-size: 110px;
    color: var(--mint-text);
  }
  .hero-art {
    position: absolute;
    left: 180px;
    top: 740px;
    width: 560px;
    height: 720px;
  }
  .variety {
    position: absolute;
    top: 1520px;
    left: 0;
    width: 100%;
    text-align: center;
    font-family: "EB Garamond", serif;
    font-weight: 700;
    font-size: 124px;
    color: var(--cocoa-text);
  }
  .weight {
    position: absolute;
    top: 1690px;
    left: 0;
    width: 100%;
    text-align: center;
    font-family: "EB Garamond", serif;
    font-weight: 700;
    font-size: 124px;
    color: var(--cocoa-text);
  }
</style>
</head>
<body>
<main class="canvas">
  <section class="wrapper">
    <header class="brand">
      <div class="brand-name"><span>Corvella</span><span class="brand-dot"></span></div>
      <p class="brand-tagline">Quality Chocolate Store</p>
    </header>

    <h1 class="flavour">MINT</h1>

    <svg class="hero-art" viewBox="0 0 560 720" role="img" aria-label="Illustration of two dark chocolate squares with fresh mint leaves in front">
      <defs>
        <linearGradient id="chocTone" x1="0" y1="0" x2="1" y2="1">
          <stop offset="0" stop-color="var(--choc-light)"/>
          <stop offset="1" stop-color="var(--choc-main)"/>
        </linearGradient>
        <radialGradient id="leafTone" cx="0.5" cy="0.5" r="0.5">
          <stop offset="0" stop-color="var(--leaf-green)"/>
          <stop offset="1" stop-color="var(--leaf-green)" stop-opacity="0"/>
        </radialGradient>
      </defs>
      <rect x="0" y="0" width="560" height="460" rx="24" fill="url(#chocTone)" opacity="0.85"/>
      <ellipse cx="300" cy="520" rx="260" ry="200" fill="url(#leafTone)"/>
    </svg>

    <p class="variety">Dark • Noir</p>
    <p class="weight">100g</p>
  </section>
</main>
</body>
</html>
```